GJ & DW Fencing Pty Ltd

We already have an existing logo created by Pixel Harbour however we have restructured to a company. We would like someone to add Pty Ltd to our business name please.

Colors

Designer to choose only greyscale colors for use in the design.

```html
<!DOCTYPE html>
<html lang="en">
<head>
<meta charset="utf-8">
<title>GJ &amp; DW Fencing Pty Ltd – Business Card</title>
<link href="https://fonts.googleapis.com/css2?family=Lato:wght@400;700&family=Merriweather:wght@700&display=swap" rel="stylesheet">
<style>
  :root {
    --backdrop: #d9d9d9;
    --card: #0d0d0d;
    --card-edge: #1a1a1a;
    --pattern-dark: #0a0a0a;
    --pattern-light: #1c1c1c;
    --ink: #ffffff;
    --ink-soft: #c9c9c9;
    --divider: #3a3a3a;
  }
  * { box-sizing: border-box; margin: 0; padding: 0; }
  html, body {
    width: 1200px;
    height: 844px;
    overflow: hidden;
    background: var(--backdrop);
  }
  .stage {
    width: 1200px;
    height: 844px;
    display: flex;
    align-items: center;
    justify-content: center;
    gap: 40px;
  }
  .card {
    width: 520px;
    height: 297px;
    background: var(--card);
    border: 1px solid var(--card-edge);
    position: relative;
    overflow: hidden;
  }
  .card-front {
    display: flex;
    align-items: center;
  }
  .brand {
    width: 230px;
    height: 100%;
    display: flex;
    align-items: center;
    justify-content: center;
    padding: 0 18px;
  }
  .brand-name {
    font-family: "Lato", sans-serif;
    font-weight: 700;
    font-size: 22px;
    line-height: 1.15;
    color: var(--ink);
    text-align: center;
    text-transform: uppercase;
    letter-spacing: 0.5px;
  }
  .divider {
    width: 1px;
    height: 150px;
    background: var(--divider);
  }
  .contact {
    padding-left: 26px;
    color: var(--ink-soft);
    font-family: "Lato", sans-serif;
    font-size: 14px;
  }
  .contact-name {
    font-family: "Merriweather", serif;
    font-weight: 700;
    font-size: 15px;
    color: var(--ink);
    letter-spacing: 0.6px;
    text-transform: uppercase;
    margin-bottom: 12px;
  }
  .contact-list { list-style: none; }
  .contact-item {
    display: flex;
    align-items: center;
    gap: 8px;
    margin-bottom: 7px;
  }
  .contact-icon {
    width: 12px;
    height: 12px;
    flex: none;
    fill: var(--ink);
  }
  .card-back .pattern {
    position: absolute;
    inset: 0;
    background:
      radial-gradient(circle at 72% 25%, var(--pattern-light) 0%, transparent 55%),
      linear-gradient(135deg, var(--pattern-light), var(--pattern-dark));
  }
</style>
</head>
<body>
  <main class="stage">
    <section class="card card-front" aria-label="Card front">
      <div class="brand">
        <p class="brand-name">GJ &amp; DW Fencing Pty Ltd</p>
      </div>
      <div class="divider"></div>
      <div class="contact">
        <h1 class="contact-name">Tom Ashgrove</h1>
        <ul class="contact-list">
          <li class="contact-item">
            <svg class="contact-icon" viewBox="0 0 12 12" aria-hidden="true">
              <path d="M2.5 0.8 L4.3 0.8 L5 3.4 L3.8 4.3 C4.4 5.7 5.6 7 7.2 7.8 L8.1 6.6 L10.8 7.3 L10.8 9.2 C10.8 10 10.2 10.6 9.4 10.5 C5 10.1 1.5 6.6 1.2 2.2 C1.1 1.4 1.7 0.8 2.5 0.8 Z"/>
            </svg>
            <span>044 5219034</span>
          </li>
          <li class="contact-item">
            <svg class="contact-icon" viewBox="0 0 12 12" aria-hidden="true">
              <path d="M0.5 2 H11.5 V10 H0.5 Z M1.4 2.8 L6 6.4 L10.6 2.8 Z" fill-rule="evenodd"/>
            </svg>
            <span>Gjdwfencing@mailbox.com</span>
          </li>
          <li class="contact-item">
            <svg class="contact-icon" viewBox="0 0 12 12" aria-hidden="true">
              <path d="M6 0.5 C3.8 0.5 2.2 2.1 2.2 4.2 C2.2 7 6 11.5 6 11.5 C6 11.5 9.8 7 9.8 4.2 C9.8 2.1 8.2 0.5 6 0.5 Z M6 2.7 A1.5 1.5 0 1 1 6 5.7 A1.5 1.5 0 1 1 6 2.7 Z" fill-rule="evenodd"/>
            </svg>
            <span>PO Box 418 Yarrowdale WA 6512</span>
          </li>
        </ul>
      </div>
    </section>

    <section class="card card-back" aria-label="Card back">
      <div class="pattern" role="img" aria-label="Tone-on-tone repeating pattern of dark animal silhouettes across the card back"></div>
    </section>
  </main>
</body>
</html>
```